Cover for Lanterns Along the Quiet Shore of Being

Cover for a book that describes everything that happens to a person, from pre-birth life plans through growing in compassion and wisdom to death and living in the afterlife. The information is revealed in messages from people living in the life after this life. The title is Lessons Gathered From Every Season of Your Existence: Shared by Voices Dwelling Beyond the Veil. Author is T. Wesley Prandt. Book size is 6 by 9.

Target Market(s)

General

Font styles to use
Serif

```html
<!DOCTYPE html>
<html lang="en">
<head>
<meta charset="utf-8">
<title>Lessons Gathered From Every Season of Your Existence — Cover</title>
<link rel="stylesheet" href="https://fonts.googleapis.com/css2?family=Cinzel:wght@400;500&family=Montserrat:wght@500&family=Cabin:wght@500&display=swap">
<style>
  :root {
    --page: #ffffff;
    --ink-deep: #07090f;
    --navy: #23256a;
    --teal: #0d7c7a;
    --teal-bright: #12908a;
    --gold: #e0a83a;
    --white: #ffffff;
    --dots: #f2f2f2;
  }
  * { margin: 0; padding: 0; box-sizing: border-box; }
  html, body {
    width: 1200px; height: 1200px; overflow: hidden;
    background: var(--page);
  }
  .cover {
    position: absolute;
    left: 240px; top: 60px;
    width: 720px; height: 1080px;
    overflow: hidden;
    color: var(--white);
  }
  .cover-art {
    position: absolute; inset: 0;
    background:
      radial-gradient(ellipse 55% 45% at 52% 40%, var(--teal-bright) 0%, var(--teal) 45%, rgba(13,124,122,0) 100%),
      radial-gradient(ellipse 80% 40% at 75% 85%, var(--navy) 0%, rgba(35,37,106,0) 100%),
      linear-gradient(180deg, #0f3b4f 0%, #0c5a63 35%, #124a66 65%, #1b2556 85%, var(--ink-deep) 100%);
  }
  .cover-content {
    position: absolute; inset: 0;
    display: flex; flex-direction: column; align-items: center;
    text-align: center;
  }
  .title {
    margin-top: 98px;
    display: flex; flex-direction: column; align-items: center;
    line-height: 1;
  }
  .title-major {
    font-family: "Cinzel", serif;
    font-weight: 500;
    font-size: 86px;
    color: var(--gold);
    letter-spacing: 0;
    margin: 6px 0 4px;
  }
  .title-minor {
    font-family: "Montserrat", sans-serif;
    font-weight: 500;
    font-size: 46px;
    color: var(--white);
    margin: 14px 0 10px;
  }
  .subtitle-block {
    position: absolute;
    left: 118px; right: 118px;
    top: 832px;
    height: 132px;
    border-top: 4px dotted var(--dots);
    border-bottom: 4px dotted var(--dots);
    display: flex; flex-direction: column; justify-content: center;
    font-family: "Cabin", sans-serif;
    font-weight: 500;
    font-size: 31px;
    line-height: 1.35;
    color: var(--gold);
    letter-spacing: 0.5px;
  }
  .author {
    position: absolute;
    left: 0; right: 0; top: 1006px;
    font-family: "Cinzel", serif;
    font-weight: 400;
    font-size: 30px;
    letter-spacing: 12px;
    color: var(--white);
  }
</style>
</head>
<body>
  <main class="cover">
    <div class="cover-art" role="img" aria-label="Abstract painted background in deep teal, blue and black watercolor washes"></div>
    <div class="cover-content">
      <h1 class="title">
        <span class="title-major">LESSONS</span>
        <span class="title-minor">GATHERED FROM</span>
        <span class="title-major">EVERY</span>
        <span class="title-minor">SEASON OF</span>
        <span class="title-major">YOUR</span>
        <span class="title-major">EXISTENCE</span>
      </h1>
      <p class="subtitle-block">
        <span class="subtitle-line">Shared by</span>
        <span class="subtitle-line">Voices Dwelling Beyond the Veil</span>
      </p>
      <p class="author">T. WESLEY PRANDT</p>
    </div>
  </main>
</body>
</html>
```